Website homepage rework for women's travel website

I have a homepage (http://www.ladies-at-the-helm.com) that I'm 50% happy with but don't want to completely overhaul. I'd like to retain a similar look but upgrade it to something a bit more modern and less old-fashioned. The basic sense of the site is empowering, self-confident, fun and adventurous - but female and over 40.

A number of the elements on the page have to be redesigned, a few can be tweaked, and a few left alone. See the rest of the brief for further information.

Target Market(s)

women over 40 who like to travel

Industry/Entity Type

Travel

Number of Pages Required

1 page

Font styles to use
Other font styles liked:
• see my brief

Requirements
Must have
• - size - the page must be significantly wider
• - the only font I MUST keep is Raleway (as in the tagline) and possibly the font of the site name (Ladies at the Helm). Both of those work for me. There are too many fonts on the page, however, and that needs to be unified.
• - the rectangles I click to get inside the site have to change to something more modern, possibly square - they do not have to be separated into two columns as they are now, nor do they need the titles (toolkit etc)
• - I like the background image of the header - but it needs to be wider of course - also keep in mind the aspect - it has to fit into the smaller inside pages, whose size will not change
• - at the end of the project I need to receive the separate elements of the design so I can eventually make a change myself if needed ie. replace my own photo, for example
Nice to have
• - the three photos need to change to something more eye-popping - or something else should take their place to fill the space
Should not have
• I do not want a full, original redesign. I want my readers to still feel as though they are on the same site - same header, mostly same fonts.

```html
<!DOCTYPE html>
<html lang="en">
<head>
<meta charset="utf-8">
<title>Ladies at the Helm</title>
<link rel="stylesheet" href="https://fonts.googleapis.com/css2?family=Raleway:wght@400;500;600&display=swap">
<style>
  :root {
    --nav-red: #a5140c;
    --brand-red: #d62a12;
    --accent-orange: #e8480c;
    --ribbon-top: #fcbf0a;
    --ribbon-bottom: #fb5a0d;
    --ink: #444444;
    --ink-soft: #5a5a5a;
    --white: #ffffff;
    --ring: #e6e6e6;
    --dark-band: #2a2622;
  }
  * { margin: 0; padding: 0; box-sizing: border-box; }
  html, body { width: 1200px; height: 2416px; overflow: hidden; background: var(--white); }
  body { position: relative; font-family: "Raleway", Arial, sans-serif; color: var(--ink); }

  .top-nav {
    position: absolute; left: 0; top: 0; width: 1200px; height: 56px;
    background: var(--nav-red); z-index: 3;
  }
  .nav-list { list-style: none; position: absolute; top: 0; left: 0; width: 100%; height: 100%; }
  .nav-list li { position: absolute; top: 20px; font-size: 13px; color: var(--white); letter-spacing: 0.2px; }

  .hero {
    position: absolute; left: 0; top: 56px; width: 1200px; height: 709px; overflow: hidden;
    background: linear-gradient(180deg, #e9901f 0%, #d26a1b 18%, #8a4a26 32%, #4b4a5c 55%, #2e3350 100%);
  }
  .hero-scene { position: absolute; inset: 0; }
  .brand { position: absolute; left: 0; top: 18px; width: 1200px; text-align: center; }
  .brand-name { font-size: 32px; font-weight: 500; color: var(--white); line-height: 42px; }
  .brand-tagline { font-size: 12px; color: #1c1c1c; margin-top: 4px; font-weight: 500; }

  .story-photo {
    position: absolute; border-radius: 50%; border: 3px solid rgba(255,255,255,0.85);
  }
  .story-label { position: absolute; color: var(--white); text-align: center; }
  .story-label .place { font-size: 15px; font-weight: 600; }
  .story-label .city { font-size: 11px; margin-top: 2px; }

  .founder-photo {
    position: absolute; left: 350px; top: 300px; width: 500px; height: 409px;
    border-radius: 240px 240px 0 0;
    background: linear-gradient(180deg, #b7b7b7 0%, #8f8f8f 45%, #c9c9c9 100%);
  }
  .slider-dots { position: absolute; left: 1159px; top: 586px; }
  .slider-dots span { display: block; width: 9px; height: 9px; border-radius: 50%; background: var(--white); margin-bottom: 12px; }
  .slider-dots span.is-active { background: var(--brand-red); }

  .intro-ribbon { position: absolute; left: 145px; top: 765px; width: 364px; height: 612px; }
  .intro-ribbon p {
    position: absolute; left: 20px; top: 135px; width: 324px; text-align: center;
    font-size: 29px; line-height: 41px; color: var(--white);
  }

  .pillar { position: absolute; left: 546px; width: 500px; height: 140px; }
  .pillar-icon {
    position: absolute; left: 0; top: 0; width: 134px; height: 134px; border-radius: 50%;
    background: #f7f7f7; border: 1px solid var(--ring);
    display: flex; align-items: center; justify-content: center;
  }
  .pillar-icon.is-filled { background: linear-gradient(180deg, #e8400f, #c4120a); border: none; }
  .pillar-title { position: absolute; left: 163px; top: 22px; font-size: 20px; font-weight: 500; color: var(--accent-orange); }
  .pillar-text { position: absolute; left: 163px; top: 60px; width: 270px; font-size: 15px; line-height: 25px; color: var(--ink-soft); }

  .guides {
    position: absolute; left: 0; top: 1485px; width: 1200px; height: 722px;
    background: linear-gradient(180deg, #4a4744 0%, #6b5d52 30%, #3a3531 65%, #1f1c1a 100%);
  }
  .guides-title { position: absolute; left: 0; top: 80px; width: 100%; text-align: center; font-size: 27px; color: var(--white); }
  .guides-link { position: absolute; left: 0; top: 133px; width: 100%; text-align: center; font-size: 11px; color: var(--white); text-decoration: underline; }

  .tile { position: absolute; width: 211px; height: 183px; }
  .tile-photo { width: 211px; height: 126px; }
  .tile-label { height: 57px; padding: 10px 14px 0; color: var(--white); }
  .tile-label h3 { font-size: 12px; font-weight: 500; text-transform: uppercase; }
  .tile-label p { font-size: 10px; margin-top: 5px; }

  .footer-social { position: absolute; top: 2257px; left: 0; width: 1200px; text-align: center; }
  .footer-social span { display: inline-block; width: 38px; height: 38px; border-radius: 50%; margin: 0 3px; background: #8c8c8c; }
  .footer-social span.is-primary { background: var(--brand-red); }
  .footer-nav { position: absolute; left: 0; top: 2327px; width: 1200px; height: 20px; list-style: none; }
  .footer-nav li { position: absolute; top: 0; font-size: 12px; color: var(--ink); }
  .copyright { position: absolute; left: 0; top: 2364px; width: 1200px; text-align: center; font-size: 11px; color: var(--ink); }
</style>
</head>
<body>

<nav class="top-nav">
  <ul class="nav-list">
    <li style="left:334px">START HERE</li>
    <li style="left:443px">ABOUT</li>
    <li style="left:503px">TRAVEL RESOURCES</li>
    <li style="left:644px">BLOG</li>
    <li style="left:707px">TRAVEL SHOP</li>
    <li style="left:806px">CONTACT</li>
  </ul>
</nav>

<header class="hero">
  <div class="hero-scene" role="img" aria-label="Desert road running toward red rock buttes under an orange sunset sky"></div>

  <div class="brand">
    <div class="brand-name">Ladies at the Helm</div>
    <div class="brand-tagline">For women who travel smart, safe + solo</div>
  </div>

  <svg width="1200" height="709" style="position:absolute;left:0;top:0" aria-hidden="true">
    <g fill="none" stroke="#ffffff" stroke-width="2" stroke-dasharray="9 7">
      <path d="M520 225 Q410 290 370 365"/>
      <path d="M680 225 Q790 290 830 365"/>
    </g>
    <g fill="none" stroke="#ffffff" stroke-width="2">
      <path d="M362 370 l8 -12 M362 370 l-8 -12"/>
      <path d="M830 370 l8 -12 M830 370 l-8 -12"/>
    </g>
  </svg>

  <div class="story-photo" role="img" aria-label="Traveller posing in a city square" style="left:520px;top:126px;width:158px;height:158px;background:linear-gradient(160deg,#c9b49a,#d8758a 60%,#9a7a66)"></div>
  <div class="story-label" style="left:690px;top:172px;width:120px;text-align:left">
    <div class="place">Clara Moss</div><div class="city">Venice,Italy</div>
  </div>

  <div class="story-photo" role="img" aria-label="Riverside old town lit at dusk" style="left:283px;top:389px;width:158px;height:158px;background:linear-gradient(180deg,#5f8fc8,#d99a4a 55%,#3a6a7a)"></div>
  <div class="story-label" style="left:135px;top:461px;width:140px;text-align:right">
    <div class="place">Streets Of Hoi An</div><div class="city">France</div>
  </div>

  <div class="story-photo" role="img" aria-label="Backpacker standing against a bright sunset" style="left:757px;top:385px;width:158px;height:158px;background:radial-gradient(circle at 50% 40%,#fff3b0,#f4b32a 45%,#c06a12)"></div>
  <div class="story-label" style="left:925px;top:458px;width:120px;text-align:left">
    <div class="place">Nina Holt</div><div class="city">Venice,Italy</div>
  </div>

  <div class="founder-photo" role="img" aria-label="Black and white portrait of the site founder"></div>

  <div class="slider-dots"><span class="is-active"></span><span></span><span></span><span></span></div>
</header>

<section class="intro">
  <svg class="intro-ribbon" width="364" height="612" viewBox="0 0 364 612" aria-hidden="true">
    <defs>
      <linearGradient id="ribbonFill" x1="0" y1="0" x2="0" y2="1">
        <stop offset="0" stop-color="#fcbf0a"/>
        <stop offset="1" stop-color="#fb5a0d"/>
      </linearGradient>
    </defs>
    <path d="M0 0 H364 V612 L182 524 L0 612 Z" fill="url(#ribbonFill)"/>
  </svg>
  <div class="intro-ribbon">
    <p>Hi, I'm Maren. I took my first solo trip at 15.<br>I'll show you how to travel...</p>
  </div>

  <div class="pillar" style="top:854px">
    <div class="pillar-icon is-filled">
      <svg width="44" height="50" viewBox="0 0 44 50" fill="none" stroke="#ffffff" stroke-width="2.5" aria-hidden="true">
        <path d="M22 3a16 16 0 0 0-9 29v6h18v-6a16 16 0 0 0-9-29z"/>
        <path d="M15 43h14M17 47h10"/>
        <path d="M18 30v-8l4 4 4-4v8"/>
      </svg>
    </div>
    <div class="pillar-title">SMART</div>
    <div class="pillar-text">Practical tools to help you plan and afford the perfect trip</div>
  </div>

  <div class="pillar" style="top:1022px">
    <div class="pillar-icon">
      <svg width="58" height="46" viewBox="0 0 58 46" aria-hidden="true">
        <rect x="20" y="2" width="18" height="9" rx="2" fill="none" stroke="#d62a12" stroke-width="3"/>
        <rect x="2" y="10" width="54" height="34" rx="4" fill="#d62a12"/>
        <rect x="2" y="24" width="54" height="3" fill="#f7f7f7"/>
        <rect x="25" y="21" width="8" height="9" fill="#f7f7f7"/>
      </svg>
    </div>
    <div class="pillar-title">SAFE</div>
    <div class="pillar-text">Down to earth advice and a ton of safety recommendations</div>
  </div>

  <div class="pillar" style="top:1200px">
    <div class="pillar-icon">
      <svg width="48" height="50" viewBox="0 0 48 50" aria-hidden="true">
        <circle cx="24" cy="13" r="11" fill="#d62a12"/>
        <path d="M2 48c0-14 10-22 22-22s22 8 22 22z" fill="#d62a12"/>
      </svg>
    </div>
    <div class="pillar-title">SOLO</div>
    <div class="pillar-text" style="top:56px">Yes, You can do it!</div>
  </div>
</section>

<section class="guides">
  <div style="position:absolute;inset:0" role="img" aria-label="Hiker with backpack raising arms on a mountain top at sunrise"></div>
  <h2 class="guides-title" style="font-weight:400">Thinking Of Solo Travel?</h2>
  <div class="guides-link">CLICK HERE TO FIND OUT HOW</div>

  <div class="tile" style="left:143px;top:214px">
    <div class="tile-photo" role="img" aria-label="Shared table of dishes" style="background:linear-gradient(135deg,#b88656,#e3c9a0)"></div>
    <div class="tile-label" style="background:#e8460f"><h3>Eating with locals</h3><p>The ultimate guide to social dining</p></div>
  </div>
  <div class="tile" style="left:377px;top:214px">
    <div class="tile-photo" role="img" aria-label="Hands packing a suitcase" style="background:linear-gradient(135deg,#f1c486,#8c6a6c)"></div>
    <div class="tile-label" style="background:#944e86"><h3>Your packing lists</h3><p>The ultimate guide to social dining</p></div>
  </div>
  <div class="tile" style="left:611px;top:214px">
    <div class="tile-photo" role="img" aria-label="Straw hat with travel accessories" style="background:linear-gradient(135deg,#a66f4a,#d98a62)"></div>
    <div class="tile-label" style="background:#f3700e"><h3>No supplement</h3><p>The ultimate guide to social dining</p></div>
  </div>
  <div class="tile" style="left:844px;top:214px">
    <div class="tile-photo" role="img" aria-label="Stressed woman at a desk" style="background:linear-gradient(135deg,#e8e8e8,#8a6a55)"></div>
    <div class="tile-label" style="background:#0a9a0e"><h3>Stress management course</h3><p>The ultimate guide to social dining</p></div>
  </div>

  <div class="tile" style="left:143px;top:426px">
    <div class="tile-photo" role="img" aria-label="Aerial view of a green city park" style="background:linear-gradient(135deg,#7c9a6a,#c4a27a)"></div>
    <div class="tile-label" style="background:#e6cf12"><h3>Solo in Argentina</h3><p>The ultimate guide to social dining</p></div>
  </div>
  <div class="tile" style="left:377px;top:426px">
    <div class="tile-photo" role="img" aria-label="Plate of fries and sauce" style="background:linear-gradient(135deg,#f4f0e8,#e2b04a)"></div>
    <div class="tile-label" style="background:#3dd9c6"><h3>Europe for foodies</h3><p>The ultimate guide to social dining</p></div>
  </div>
  <div class="tile" style="left:611px;top:426px">
    <div class="tile-photo" role="img" aria-label="Backpacker on a hillside trail" style="background:linear-gradient(135deg,#9ab8d0,#5f7a4a)"></div>
    <div class="tile-label" style="background:#d21a18"><h3>Solo female travel</h3><p>The ultimate guide to social dining</p></div>
  </div>
  <div class="tile" style="left:844px;top:426px">
    <div class="tile-photo" role="img" aria-label="Protester with a megaphone" style="background:linear-gradient(135deg,#c42a2a,#e0c0b0)"></div>
    <div class="tile-label" style="background:#3aa3ee"><h3>Rebellious carouge</h3><p>The ultimate guide to social dining</p></div>
  </div>
</section>

<footer>
  <div class="footer-social" aria-label="Social links">
    <span class="is-primary"></span><span></span><span></span>
  </div>
  <ul class="footer-nav">
    <li style="left:334px">START HERE</li>
    <li style="left:443px">ABOUT</li>
    <li style="left:503px">TRAVEL RESOURCES</li>
    <li style="left:644px">BLOG</li>
    <li style="left:707px">TRAVEL SHOP</li>
    <li style="left:806px">CONTACT</li>
  </ul>
  <div class="copyright">© 2016 COMPANY NAME &nbsp;|&nbsp; ALL RIHGTS RESERVED</div>
</footer>

</body>
</html>
```